Business Card Design Project

Industry/Entity Type

Business

Contact Information for Business Card

The Ardenfield Gospel Choir
Desmond Fairley, Minister of Music

The Grace Harbor Fellowship of Mount Orla
Founded 1836

Twitter @ardenfieldchoir
Instagram ardenfieldgc
Facebook socialhub-net.com/afgc382
Website: ardenfieldgc.org
For Bookings: (555) 274-AFGC
2748 Merrow Street, Calloway Bay, WA 98520

Back of the Card
Music and Cd's Recordings Available On
Choirs Website and Also
Tunevault, Corvex Sound, Disc Sprout (the music online logo)

```html
<!DOCTYPE html>
<html lang="en">
<head>
<meta charset="utf-8">
<title>The Ardenfield Gospel Choir – Business Card</title>
<link rel="stylesheet" href="https://fonts.googleapis.com/css2?family=Roboto:wght@400;500;700&family=Roboto+Condensed:wght@400;700&family=Tinos:ital@1&display=swap">
<style>
  :root {
    --page-bg: #e9e6e1;
    --card-white: #ffffff;
    --choir-red: #d8343f;
    --brand-blue: #1d5fb0;
    --back-blue: #1a66b2;
    --back-blue-dark: #135499;
    --text-grey: #555a60;
    --text-white: #ffffff;
  }
  * { box-sizing: border-box; margin: 0; padding: 0; }
  html, body { width: 1200px; height: 911px; overflow: hidden; }
  body {
    background: var(--page-bg);
    font-family: "Roboto", Arial, sans-serif;
    position: relative;
  }
  .card {
    position: absolute;
    width: 700px;
    height: 400px;
    border-radius: 22px;
    overflow: hidden;
    box-shadow: 0 10px 28px rgba(0,0,0,.22);
  }
  /* Front */
  .card-front { left: 60px; top: 40px; background: var(--card-white); }
  .corner-tab {
    position: absolute; right: 0; top: 0;
    width: 34px; height: 14px;
    background: var(--brand-blue);
    border-bottom-left-radius: 10px;
  }
  .holder { position: absolute; right: 46px; top: 56px; text-align: right; }
  .holder-name {
    font-family: "Roboto Condensed", Arial, sans-serif;
    font-weight: 700; font-size: 30px; color: var(--choir-red); letter-spacing: .5px;
  }
  .holder-role {
    font-family: "Roboto Condensed", Arial, sans-serif;
    font-size: 17px; color: var(--brand-blue); letter-spacing: .5px;
  }
  .identity { position: absolute; left: 40px; top: 136px; display: flex; gap: 18px; align-items: center; }
  .logo-mark {
    display: flex; align-items: center; gap: 8px;
    font-family: "Roboto", Arial, sans-serif; font-weight: 700;
    font-size: 15px; color: var(--brand-blue);
  }
  .logo-dot { width: 30px; height: 30px; border-radius: 50%; background: var(--brand-blue); flex: none; }
  .choir-name {
    font-family: "Tinos", "Times New Roman", serif; font-style: italic;
    font-size: 26px; color: var(--choir-red);
  }
  .minister { font-size: 16px; font-weight: 700; color: var(--brand-blue); margin-top: 2px; }
  .church { font-size: 12px; color: var(--text-grey); margin-top: 4px; }
  .founded { font-size: 12px; color: var(--text-grey); margin-top: 2px; }
  .contacts { position: absolute; left: 48px; top: 246px; list-style: none; }
  .contacts li {
    display: flex; align-items: center; gap: 10px;
    font-size: 15px; color: var(--text-grey); line-height: 21px;
  }
  .contacts svg { width: 13px; height: 13px; flex: none; }
  /* Back */
  .card-back {
    left: 440px; top: 470px;
    background: radial-gradient(circle at 55% 40%, #2a79c4 0%, var(--back-blue) 45%, var(--back-blue-dark) 100%);
    color: var(--text-white);
  }
  .back-logo {
    position: absolute; left: 0; right: 0; top: 84px;
    display: flex; align-items: center; justify-content: center; gap: 12px;
    font-weight: 700; font-size: 20px;
  }
  .back-logo-dot { width: 44px; height: 44px; border-radius: 50%; background: var(--text-white); }
  .back-message {
    position: absolute; left: 0; right: 0; top: 190px; text-align: center;
    font-family: "Tinos", "Times New Roman", serif; font-style: italic;
    font-size: 24px; line-height: 32px;
  }
  .stores { position: absolute; left: 0; right: 0; top: 284px; display: flex; justify-content: center; gap: 18px; list-style: none; }
  .stores li {
    border: 2px solid var(--text-white); border-radius: 22px;
    padding: 8px 20px; font-size: 15px; font-weight: 500;
  }
</style>
</head>
<body>
  <section class="card card-front">
    <div class="corner-tab"></div>
    <div class="holder">
      <p class="holder-name">JORDAN VALE</p>
      <p class="holder-role">CEO/FOUNDER</p>
    </div>
    <div class="identity">
      <div class="logo-mark"><span class="logo-dot"></span>Ardenfield</div>
      <div>
        <p class="choir-name">The Ardenfield Gospel Choir</p>
        <p class="minister">Desmond Fairley, Minister of Music</p>
        <p class="church">The Grace Harbor Fellowship of Mount Orla</p>
        <p class="founded">Founded 1836</p>
      </div>
    </div>
    <ul class="contacts">
      <li><svg viewBox="0 0 12 12"><circle cx="6" cy="6" r="6" fill="#d8343f"/></svg>@ardenfieldchoir</li>
      <li><svg viewBox="0 0 12 12"><rect width="12" height="12" rx="2" fill="#d8343f"/></svg>ardenfieldgc</li>
      <li><svg viewBox="0 0 12 12"><rect width="12" height="12" rx="2" fill="#d8343f"/></svg>socialhub-net.com/afgc382</li>
      <li><svg viewBox="0 0 24 24"><path fill="#d8343f" d="M6.6 10.8c1.4 2.8 3.8 5.1 6.6 6.6l2.2-2.2c.3-.3.7-.4 1-.2 1.1.4 2.3.6 3.6.6.6 0 1 .4 1 1V20c0 .6-.4 1-1 1C10.6 21 3 13.4 3 4c0-.6.4-1 1-1h3.5c.6 0 1 .4 1 1 0 1.3.2 2.5.6 3.6.1.3 0 .7-.2 1z"/></svg>(555) 274-AFGC (Bookings)</li>
      <li><svg viewBox="0 0 12 12"><circle cx="6" cy="6" r="5" fill="none" stroke="#d8343f" stroke-width="2"/></svg>www.ardenfieldgc.org</li>
      <li><svg viewBox="0 0 24 24"><path fill="#d8343f" d="M12 2C8.1 2 5 5.1 5 9c0 5.2 7 13 7 13s7-7.8 7-13c0-3.9-3.1-7-7-7zm0 9.5a2.5 2.5 0 1 1 0-5 2.5 2.5 0 0 1 0 5z"/></svg>2748 Merrow Street, Calloway Bay, WA 98520</li>
    </ul>
  </section>

  <section class="card card-back">
    <div class="back-logo"><span class="back-logo-dot"></span>Ardenfield</div>
    <p class="back-message">Music and Cd's Recordings Available On<br>Choirs Website and Also</p>
    <ul class="stores">
      <li>Tunevault</li>
      <li>Corvex Sound</li>
      <li>Disc Sprout</li>
    </ul>
  </section>
</body>
</html>
```